Design the Business card for NetVaultic

Business card required for a professional Cyber Security business.
Company Logo and Icon has already been provided however I would like other options for the logo and icon to compare to. Alternatively, please refine/enhance the image of the logo.icon I have already provided.

If you are going to use the provided logo and icon, I was thinking that the company raised Logo on White background would serve well on the front of the card. See attached. AND, a large company raised stand-alone icon to appear on black background on the back of the card with tagline 'Cyber Risk Management, Governance and Consulting' or 'Cyber Security for your Business' See attached.
Alternatively, provide your own design for the logo and icon.

Target Market(s)

Enterprise, Government, Financial.

Contact Information for Business Card

Tavin Orloweth
Founder and CEO

Email Address
Mobile Number
Website URL
LinkedIn URL

Logo Text

NetVaultic - see attached example of logo

Font styles to use
Other font styles liked:
• Berlin Sans FB

Requirements
Must have
• Clean large and bold icon on the back with tagline.
• Horizontal alignment,
Nice to have
• Round edges.
• Raised Logo/Icon
Should not have
• An unprofessional look and feel.

```html
<!DOCTYPE html>
<html lang="en">
<head>
<meta charset="utf-8">
<title>NetVaultic Business Card</title>
<link rel="stylesheet" href="https://fonts.googleapis.com/css2?family=Signika:wght@500;600&family=Roboto:wght@400&display=swap">
<style>
  :root {
    --stage: #2b2b2b;
    --card-light: #f4f4f4;
    --card-dark: #1b1c1e;
    --brand-blue: #1a6fc0;
    --soft-blue: #4a76c6;
    --brand-yellow: #f5b800;
    --ink: #4a4a4a;
  }
  html, body {
    margin: 0;
    padding: 0;
    width: 1200px;
    height: 960px;
    overflow: hidden;
    background: var(--stage);
  }
  .canvas {
    position: relative;
    width: 1200px;
    height: 960px;
  }
  .card {
    position: absolute;
    box-shadow: 0 4px 12px rgba(0,0,0,0.5);
  }
  .card--front {
    left: 314px; top: 113px; width: 600px; height: 343px;
    background: var(--card-light);
  }
  .card--back {
    left: 311px; top: 472px; width: 602px; height: 343px;
    background: var(--card-dark);
  }
  .emblem-area {
    position: absolute;
    left: 40px; top: 20px;
    width: 300px; height: 300px;
    border-radius: 50%;
    background: var(--soft-blue);
  }
  .wordmark {
    position: absolute;
    font-family: "Signika", sans-serif;
    font-weight: 600;
    color: var(--brand-blue);
    margin: 0;
    line-height: 1;
    white-space: nowrap;
  }
  .card--front .wordmark {
    right: 40px; top: 57px;
    font-size: 41px;
  }
  .person {
    position: absolute;
    right: 42px; top: 168px;
    text-align: right;
    font-family: "Signika", sans-serif;
  }
  .person__name {
    margin: 0;
    font-size: 21px;
    font-weight: 500;
    color: var(--brand-blue);
    line-height: 1.1;
  }
  .person__role {
    margin: 0;
    font-size: 15px;
    font-weight: 500;
    color: var(--brand-yellow);
    line-height: 1.2;
  }
  .accent-tab {
    position: absolute;
    right: 0; top: 171px;
    width: 12px; height: 35px;
    background: var(--brand-blue);
  }
  .contacts {
    position: absolute;
    right: 42px; top: 225px;
    margin: 0; padding: 0;
    list-style: none;
    font-family: "Roboto", sans-serif;
    font-size: 14.5px;
    color: var(--ink);
    text-align: right;
  }
  .contacts li {
    height: 19px;
    line-height: 19px;
    display: flex;
    justify-content: flex-end;
    align-items: center;
    gap: 6px;
  }
  .contacts svg { width: 13px; height: 13px; flex: none; }
  .back-brand {
    position: absolute;
    left: 125px; top: 114px;
    display: flex;
    align-items: center;
    gap: 12px;
  }
  .back-brand__dot {
    width: 84px; height: 84px;
    border-radius: 50%;
    background: var(--soft-blue);
  }
  .card--back .wordmark {
    position: static;
    font-size: 50px;
    font-weight: 500;
  }
  .tagline {
    position: absolute;
    left: 0; right: 0; top: 277px;
    margin: 0;
    text-align: center;
    font-family: "Signika", sans-serif;
    font-weight: 500;
    font-size: 18px;
  }
  .tagline__primary { color: var(--soft-blue); }
  .tagline__secondary { color: var(--brand-yellow); }
</style>
</head>
<body>
<main class="canvas">
  <section class="card card--front">
    <div class="emblem-area" role="img" aria-label="Company emblem area"></div>
    <h1 class="wordmark">NetVaultic</h1>
    <div class="person">
      <p class="person__name">Tavin Orloweth</p>
      <p class="person__role">Founder &amp; CEO</p>
    </div>
    <div class="accent-tab"></div>
    <ul class="contacts">
      <li>604 218 7391
        <svg viewBox="0 0 13 13"><rect x="3" y="0.5" width="7" height="12" rx="1.3" fill="none" stroke="#1a6fc0" stroke-width="1.4"/><rect x="5.5" y="10" width="2" height="1" fill="#1a6fc0"/></svg>
      </li>
      <li>tavin@netvaultic.com
        <svg viewBox="0 0 13 13"><rect x="0.5" y="3" width="12" height="8" fill="#1a6fc0"/><path d="M0.5 3 L6.5 7.5 L12.5 3" fill="none" stroke="#fff" stroke-width="1"/></svg>
      </li>
      <li>www.netvaultic.com
        <svg viewBox="0 0 13 13"><circle cx="6.5" cy="6.5" r="6" fill="#1a6fc0"/><path d="M6.5 0.5 V12.5 M0.5 6.5 H12.5" stroke="#fff" stroke-width="0.9"/></svg>
      </li>
      <li>netvaultic
        <svg viewBox="0 0 13 13"><circle cx="6.5" cy="6.5" r="6" fill="#1a6fc0"/></svg>
      </li>
    </ul>
  </section>

  <section class="card card--back">
    <div class="back-brand">
      <div class="back-brand__dot"></div>
      <h2 class="wordmark">NetVaultic</h2>
    </div>
    <p class="tagline"><span class="tagline__primary">Cyber Risk Management,</span> <span class="tagline__secondary">Governance &amp; Consulting</span></p>
  </section>
</main>
</body>
</html>
```